Real Estate Brokerage Stationery Designs

I am looking to have presentation folders with business card slots on both sides along with pockets on both sides. I've attached logos, website colors along with current business card designs.

I am looking for envelope designs both big and small. Possibly new business card designs, notepad templates for big and small notepads. Letterhead designs. Pop socket designs. Realtors name badge designs.

www.brightholdrealty.example

```html
<!DOCTYPE html>
<html lang="en">
<head>
<meta charset="utf-8">
<title>Brighthold Realty – Presentation Folder</title>
<link rel="stylesheet" href="https://fonts.googleapis.com/css2?family=Montserrat:wght@500;600;700&display=swap">
<style>
  :root {
    --blue: #0553a5;
    --blue-deep: #044a95;
    --blue-light: #1f77d2;
    --shadow-grey: #a8a8a8;
    --paper: #f1f1f1;
    --paper-shade: #dedede;
    --ink: #1a1a1a;
    --muted: #9a9a9a;
    --backdrop: #d9d9d9;
    --white: #ffffff;
  }
  * { margin: 0; padding: 0; box-sizing: border-box; }
  html, body { width: 1200px; height: 1200px; overflow: hidden; }
  body {
    background: var(--backdrop);
    font-family: "Montserrat", sans-serif;
    position: relative;
  }
  .folder-spread {
    position: absolute;
    left: 100px; top: 270px;
    width: 1000px; height: 660px;
  }
  .folder-art { position: absolute; inset: 0; }
  .brand-mark {
    position: absolute;
    left: 560px; top: 300px; width: 380px;
    display: flex; align-items: center; justify-content: center; gap: 14px;
  }
  .brand-mark__square {
    width: 22px; height: 22px; background: var(--blue);
  }
  .brand-mark__name {
    font-weight: 700; font-size: 34px; color: var(--ink);
    letter-spacing: 0.5px;
  }
  .front-web {
    position: absolute;
    left: 560px; top: 568px; width: 380px; text-align: center;
    color: var(--white); font-size: 13px; font-weight: 600;
  }
  .back-contact {
    position: absolute;
    left: 52px; top: 540px;
    color: var(--white); font-size: 10.5px; font-weight: 600; line-height: 1.45;
  }
  .back-contact__address { margin-bottom: 4px; }
  .back-contact__line { display: flex; align-items: center; gap: 8px; }
  .back-contact__line svg { width: 10px; height: 10px; flex: none; }
</style>
</head>
<body>
  <main class="folder-spread">
    <svg class="folder-art" viewBox="0 0 1000 660" width="1000" height="660" aria-hidden="true">
      <defs>
        <linearGradient id="paperFade" x1="0" y1="0" x2="1" y2="0">
          <stop offset="0" stop-color="#ffffff"/>
          <stop offset="0.5" stop-color="#e6e6e6"/>
          <stop offset="1" stop-color="#f3f3f3"/>
        </linearGradient>
      </defs>
      <rect class="paper" width="1000" height="660" fill="url(#paperFade)"/>
      <!-- top swoop -->
      <path class="top-shadow" fill="var(--shadow-grey)"
        d="M0 0 H1000 C880 175 660 235 500 268 C320 300 150 305 0 318 Z"/>
      <path class="top-stripe" fill="var(--blue-light)"
        d="M0 0 H1000 C880 160 660 222 500 255 C320 288 150 292 0 304 Z"/>
      <path class="top-band" fill="var(--blue)"
        d="M0 0 H1000 C900 110 680 185 500 215 C320 250 150 270 0 300 Z"/>
      <!-- bottom band -->
      <path class="bottom-stripe" fill="var(--blue-light)"
        d="M0 440 C200 455 380 490 500 508 C700 500 850 480 1000 430 V660 H0 Z"/>
      <path class="bottom-band" fill="var(--blue)"
        d="M0 452 C200 467 380 502 500 522 C700 514 850 494 1000 458 V660 H0 Z"/>
      <!-- spine fold -->
      <line class="spine" x1="500" y1="0" x2="500" y2="660" stroke="#000" stroke-opacity="0.12" stroke-width="2"/>
    </svg>

    <div class="brand-mark">
      <span class="brand-mark__square"></span>
      <span class="brand-mark__name">Brighthold Realty</span>
    </div>

    <p class="front-web">www.brightholdrealty.example</p>

    <address class="back-contact" style="font-style:normal">
      <p class="back-contact__address">742 Harbor Point Ave,<br>Suite 310, Coral Vista,<br>FL 30000</p>
      <p class="back-contact__line">
        <svg viewBox="0 0 10 10"><rect x="2.5" y="0.5" width="5" height="9" rx="1" fill="none" stroke="#fff" stroke-width="1"/></svg>
        555-201-4417
      </p>
      <p class="back-contact__line">
        <svg viewBox="0 0 10 10"><path d="M2 1 L4 3 L3 4 Q4.5 6 6 7 L7 6 L9 8 L8 9.5 Q2 8 0.5 2 Z" fill="#fff"/></svg>
        555-318-2960
      </p>
      <p class="back-contact__line">
        <svg viewBox="0 0 10 10"><rect x="0.5" y="3" width="9" height="6" fill="none" stroke="#fff" stroke-width="1"/><rect x="2.5" y="0.5" width="5" height="3" fill="#fff"/></svg>
        555-476-0832
      </p>
      <p class="back-contact__line">
        <svg viewBox="0 0 10 10"><circle cx="5" cy="5" r="4.3" fill="none" stroke="#fff" stroke-width="1"/><path d="M0.7 5 H9.3 M5 0.7 Q2 5 5 9.3 M5 0.7 Q8 5 5 9.3" fill="none" stroke="#fff" stroke-width="0.8"/></svg>
        www.brightholdrealty.example
      </p>
    </address>
  </main>
</body>
</html>
```